Publishing House

Amber Heron
Exotic, they weave silk out of nowhere. Blessed with a keen sense. Sophisticated discernment. Fearsome reputation. Powerful, but do not harm. Unless, you really needle them. Believe in continuous improvement. A young tarantula may shed its exoskeleton periodically in order to grow, a process called molting : several times a year as a part of the maturation process.
White. The colour pristine. Everything pure. Blemish-free. We feel for the writer. We want to infuse spurt of purity into publishing.
We, at Amber Heron Publishing, are here to question the status-quo, to provide a fresh, invigorating platform for writers to reach their art to their readership via processes that are transparent, impartial and non-discriminatory, and a level of transparency that will set new benchmarks in the world of publishing.
We bring to you new concepts in the areas of editing, proof-reading and cover-designing. Our suite of marketing services targets new, and web-based methods as well as traditional methods.
It is time the writer got his or her due!

I have attached our logo also

Industry/Entity Type

House

```html
<!DOCTYPE html>
<html lang="en">
<head>
<meta charset="utf-8">
<title>Amber Heron Publishing – Cover</title>
<link rel="stylesheet" href="https://fonts.googleapis.com/css2?family=Audiowide&display=swap">
<style>
  :root {
    --page-bg: #eceff3;
    --parchment-light: #f6e2b4;
    --parchment-mid: #e9b86f;
    --parchment-deep: #c9762a;
    --headline-brown: #5b2c0c;
    --frame-white: #ffffff;
    --frame-line: #c4c9d2;
    --tile-black: #1f1c1c;
    --logo-gold: #d8b56a;
    --bag-kraft: #c99a5f;
    --bag-shade: #a87a42;
  }
  * { box-sizing: border-box; margin: 0; padding: 0; }
  html, body {
    width: 1200px;
    height: 718px;
    overflow: hidden;
    background: var(--page-bg);
  }
  .canvas {
    position: relative;
    width: 1200px;
    height: 718px;
  }
  .cover {
    position: absolute;
    left: 35px;
    top: 52px;
    width: 1158px;
    height: 422px;
    overflow: hidden;
    background:
      radial-gradient(ellipse 45% 60% at 45% 60%, var(--parchment-light) 0%, rgba(246,226,180,0) 100%),
      radial-gradient(ellipse 80% 90% at 40% 50%, var(--parchment-mid) 0%, var(--parchment-deep) 100%);
  }
  .headline {
    position: absolute;
    left: 39px;
    top: 100px;
    font-family: "Audiowide", sans-serif;
    font-weight: 400;
    font-size: 36px;
    line-height: 60px;
    color: var(--headline-brown);
    letter-spacing: 0;
    white-space: nowrap;
    text-transform: uppercase;
  }
  .books-in-bag {
    position: absolute;
    left: 701px;
    top: 37px;
    width: 408px;
    height: 385px;
    background:
      linear-gradient(180deg,
        rgba(0,0,0,0) 0%, rgba(0,0,0,0) 38%,
        var(--bag-kraft) 38%, var(--bag-shade) 100%),
      linear-gradient(90deg, #e4622a 0%, #d8342a 30%, #2aa24a 55%, #1e9ed8 80%, #2aa24a 100%);
    border-radius: 4px;
  }
  .profile-tile {
    position: absolute;
    left: 67px;
    top: 312px;
    width: 230px;
    height: 229px;
    background: var(--frame-white);
    border: 1px solid var(--frame-line);
    padding: 7px;
  }
  .profile-tile__inner {
    width: 100%;
    height: 100%;
    background: var(--tile-black);
    display: flex;
    align-items: center;
    justify-content: center;
  }
  .brand-name {
    font-family: "Audiowide", sans-serif;
    font-size: 22px;
    color: var(--logo-gold);
    letter-spacing: 1px;
    white-space: nowrap;
  }
</style>
</head>
<body>
  <main class="canvas">
    <section class="cover">
      <h1 class="headline">All Publisher Solutions<br>In Under One Roof</h1>
      <div class="books-in-bag" role="img" aria-label="Illustration of colourful books standing in a kraft paper shopping bag"></div>
    </section>
    <div class="profile-tile">
      <div class="profile-tile__inner">
        <span class="brand-name">Amber Heron</span>
      </div>
    </div>
  </main>
</body>
</html>
```